Business Card for a mobile physiotherapy company

I need a layout for a business card for a mobile physiotherapy company.
Slogan is "Mobile Physiotherapy - Your Road To Recovery"
Phone number is 867-555-0142
Email VardenTherapy@postnest.ca (subject to change with website)
Website www.VardenTherapy.ca
My name and credentials: Luke Varden Luke Varden, BSc(kin), MPT, CAFCI, IMS
Information maybe included: Direct Billing, Services including Physiotherapy, IMS, acupuncture
Maybe include facebook and instagram logos
One side with the logo clean and sharp
Other side with details, try not to look too busy, keep everything concise

```html
<!DOCTYPE html>
<html lang="en">
<head>
<meta charset="utf-8">
<title>Varden Therapy – Business Card</title>
<link rel="stylesheet" href="https://fonts.googleapis.com/css2?family=Tinos:wght@700&family=Open+Sans:wght@400;600&display=swap">
<style>
  :root{
    --navy:#2c4770;
    --green:#0b5345;
    --ink:#1f1f1f;
    --white:#ffffff;
    --rule:#c8c8c8;
    --bg-light:#e6e7e9;
    --bg-dark:#b4b5b8;
  }
  *{box-sizing:border-box;margin:0;padding:0}
  html,body{width:1200px;height:1113px;overflow:hidden}
  body{
    position:relative;
    background:linear-gradient(90deg,var(--bg-light) 0%,#cfd0d3 60%,var(--bg-dark) 100%);
    font-family:"Open Sans",Arial,sans-serif;
  }
  .card{position:absolute;width:767px;height:439px;border-radius:22px;overflow:hidden}
  .card-front{left:83px;top:91px;background:var(--white);border:1px solid #bdbdbd}
  .card-back{left:350px;top:587px;background:var(--navy)}

  .brand-name{
    position:absolute;text-align:center;
    font-family:"Open Sans",Arial,sans-serif;font-weight:600;
    font-size:38px;line-height:1.2;white-space:nowrap;
  }
  .card-front .brand-name{left:20px;width:380px;top:140px;color:var(--navy)}
  .card-back .brand-name{left:0;width:767px;top:205px;color:var(--white);font-size:46px}

  .divider{position:absolute;left:404px;top:40px;width:2px;height:257px;background:var(--rule)}

  .details{position:absolute;left:437px;top:34px}
  .person-name{font-family:"Tinos","Times New Roman",serif;font-weight:700;font-size:26px;color:var(--navy);letter-spacing:1px;line-height:1.1}
  .credentials{font-size:14.5px;color:var(--ink);margin-top:3px}
  .contact-list{list-style:none;margin-top:16px}
  .contact-list li{display:flex;align-items:center;gap:8px;font-size:19px;color:var(--ink);height:32px}
  .contact-list svg{width:19px;height:19px;flex:none}
  .services-title{font-weight:600;font-size:19px;color:var(--navy);margin-top:14px}
  .services{display:grid;grid-template-columns:auto auto;column-gap:14px;row-gap:2px;margin-top:6px;list-style:none;width:300px}
  .services li{font-size:19px;color:var(--green);white-space:nowrap}
  .services li::before{content:"•";font-size:13px;margin-right:5px;vertical-align:2px}

  .footer-band{
    position:absolute;left:0;top:362px;width:767px;height:77px;
    background:linear-gradient(90deg,var(--green) 0%,var(--navy) 45%,var(--navy) 100%);
  }
  .tagline{position:absolute;left:437px;width:330px;top:370px;text-align:center;color:var(--white);font-family:"Tinos","Times New Roman",serif;font-weight:700;font-size:20.5px;line-height:31px}

  .social{position:absolute;left:0;width:767px;top:345px;display:flex;justify-content:center;gap:26px}
  .social-item{display:flex;align-items:center;gap:11px;color:var(--white);font-size:22px}
  .social-item .mark{width:48px;height:48px;background:var(--white);border-radius:7px}
</style>
</head>
<body>

<section class="card card-front" aria-label="Business card front">
  <p class="brand-name">Varden Therapy</p>
  <div class="divider"></div>

  <div class="details">
    <h1 class="person-name">LUKE VARDEN</h1>
    <p class="credentials">BSc(kin), MPT, CAFCI, IMS</p>
    <ul class="contact-list">
      <li><svg viewBox="0 0 20 20"><circle cx="10" cy="10" r="8.6" fill="none" stroke="var(--navy)" stroke-width="1.6"/><path d="M7,5.5 L8.6,5.5 L9.4,8 L8.3,9 C8.9,10.4 9.7,11.2 11,11.8 L12,10.7 L14.5,11.5 L14.5,13 C11,13.6 6.4,9 7,5.5 Z" fill="var(--navy)"/></svg>867-555-0142</li>
      <li><svg viewBox="0 0 20 20"><circle cx="10" cy="10" r="8.6" fill="none" stroke="var(--navy)" stroke-width="1.6"/><rect x="5.5" y="7" width="9" height="6.5" rx="1" fill="var(--navy)"/><path d="M5.8,7.4 L10,10.6 L14.2,7.4" fill="none" stroke="var(--white)" stroke-width="1"/></svg>VardenTherapy@postnest.ca</li>
      <li><svg viewBox="0 0 20 20" fill="none" stroke="var(--navy)" stroke-width="1.3"><circle cx="10" cy="10" r="8.4"/><ellipse cx="10" cy="10" rx="3.8" ry="8.4"/><path d="M1.6,10 H18.4 M3,5.8 H17 M3,14.2 H17"/></svg>www.VardenTherapy.ca</li>
    </ul>
    <h2 class="services-title">Services Including</h2>
    <ul class="services">
      <li>Physiotherapy</li><li>Direct Billing</li>
      <li>Ims</li><li>Acupuncture</li>
    </ul>
  </div>

  <div class="footer-band" role="img" aria-label="Flowing navy and green wave band along the bottom of the card"></div>
  <p class="tagline">Mobile Physiotherapy<br>Your Road To Recovery</p>
</section>

<section class="card card-back" aria-label="Business card back">
  <p class="brand-name">Varden Therapy</p>
  <div class="social">
    <div class="social-item"><span class="mark"></span>VardenTherapy</div>
    <div class="social-item"><span class="mark"></span>@VardenTherapy</div>
  </div>
</section>

</body>
</html>
```